Business card for Luxury Portable Restroom Trailer company

We are a Luxury Portable Restroom Trailer Company Called FALCRIDGE HIRES. Based in Orange County California. We provide portable restroom trailers for events, such as, Weddings, Concerts, Charity events, Sporting events, Tournaments, Corporate events, ect. We rent and Sell the Luxury restrooms. Our colors are white, grey, and Orange. As you will see in the logo we uploaded.
There are 2 people in the company so the names and titles will change for the 3 people but card will remain the same. Here is the information for each Person: Dwight Penner CFO 555 318-0476
next Person: Leon Marchetti VP 555 318-0476
Next Person: Owen Marchetti CEO 555 318-0476
Information to include on the card: Luxury Restroom Trailers Rental and Sales. Weddings, Concerts, Charity, Sporting and Corp. Events.

```html
<!DOCTYPE html>
<html lang="en">
<head>
<meta charset="utf-8">
<title>Falcridge Hires — Business Card</title>
<link href="https://fonts.googleapis.com/css2?family=Montserrat:wght@400;500;700;800&display=swap" rel="stylesheet">
<style>
  :root {
    --stage: #1c1c1d;
    --card-top: #4a4b4d;
    --card-bottom: #2e2f31;
    --orange: #f26b21;
    --white: #f4f4f4;
    --muted: #d9d9d9;
    --ghost: #5a5b5e;
  }
  * { margin: 0; padding: 0; box-sizing: border-box; }
  html, body { width: 1200px; height: 1200px; overflow: hidden; }
  body {
    background: var(--stage);
    font-family: "Montserrat", sans-serif;
    display: flex;
    flex-direction: column;
    align-items: center;
    justify-content: center;
    gap: 56px;
  }
  .card {
    position: relative;
    width: 900px;
    height: 514px;
    overflow: hidden;
    border-radius: 4px;
    background: radial-gradient(ellipse at 45% 35%, var(--card-top), var(--card-bottom) 75%);
    box-shadow: 0 18px 40px rgba(0,0,0,0.55);
  }
  .ghost-ring {
    position: absolute;
    border-radius: 50%;
    border: 22px solid var(--ghost);
    background: rgba(0,0,0,0.08);
    opacity: 0.75;
  }
  .card--back .ghost-ring { width: 500px; height: 500px; right: -160px; bottom: -250px; }
  .card--front .ghost-ring { width: 560px; height: 560px; left: -200px; top: -260px; }

  .wordmark {
    position: absolute;
    display: flex;
    align-items: center;
    gap: 14px;
  }
  .wordmark__mark {
    width: 22px; height: 22px;
    background: var(--orange);
  }
  .wordmark__name {
    font-weight: 800;
    font-size: 40px;
    letter-spacing: 1px;
    color: var(--white);
    line-height: 1;
  }

  .card--back .wordmark { left: 70px; top: 290px; }
  .tagline {
    position: absolute;
    left: 330px;
    top: 62px;
  }
  .tagline__lead {
    color: var(--orange);
    font-weight: 700;
    font-size: 22px;
    margin-bottom: 8px;
  }
  .tagline__services {
    color: var(--white);
    font-weight: 500;
    font-size: 20px;
  }
  .tagline__services .sep { color: var(--orange); margin: 0 6px; }

  .card--front .wordmark { left: 400px; top: 70px; }
  .contact { position: absolute; left: 400px; top: 150px; }
  .contact__name {
    color: var(--orange);
    font-weight: 700;
    font-size: 38px;
    line-height: 1.1;
  }
  .contact__title {
    color: var(--white);
    font-size: 22px;
    font-weight: 400;
    margin-bottom: 18px;
  }
  .contact__address {
    color: var(--white);
    font-size: 22px;
    line-height: 1.3;
    margin-bottom: 18px;
  }
  .contact__list { list-style: none; }
  .contact__item {
    display: flex;
    align-items: center;
    gap: 12px;
    color: var(--white);
    font-size: 22px;
    line-height: 1.45;
  }
  .contact__icon { width: 18px; height: 18px; flex: none; }
</style>
</head>
<body>

  <section class="card card--back" aria-label="Card back">
    <div class="ghost-ring" aria-hidden="true"></div>
    <div class="tagline">
      <p class="tagline__lead">Luxury Restroom Trailers Rental and Sales</p>
      <p class="tagline__services">Weddings<span class="sep">|</span>Concerts<span class="sep">|</span>Charity<span class="sep">|</span>Sporting<span class="sep">|</span>Corp. Events</p>
    </div>
    <div class="wordmark">
      <span class="wordmark__mark" aria-hidden="true"></span>
      <span class="wordmark__name">FALCRIDGE HIRES</span>
    </div>
  </section>

  <section class="card card--front" aria-label="Card front">
    <div class="ghost-ring" aria-hidden="true"></div>
    <div class="wordmark">
      <span class="wordmark__mark" aria-hidden="true"></span>
      <span class="wordmark__name">FALCRIDGE HIRES</span>
    </div>
    <div class="contact">
      <p class="contact__name">Dwight Penner</p>
      <p class="contact__title">CFO</p>
      <p class="contact__address">4807 Alder Crest Road Lake<br>Bellmont Maine 04219</p>
      <ul class="contact__list">
        <li class="contact__item">
          <svg class="contact__icon" viewBox="0 0 24 24" aria-hidden="true"><path fill="var(--orange)" d="M6.6 10.8a15 15 0 0 0 6.6 6.6l2.2-2.2a1 1 0 0 1 1-.25 11.4 11.4 0 0 0 3.6.57 1 1 0 0 1 1 1V20a1 1 0 0 1-1 1A17 17 0 0 1 3 4a1 1 0 0 1 1-1h3.5a1 1 0 0 1 1 1c0 1.25.2 2.45.57 3.57a1 1 0 0 1-.25 1z"/></svg>
          555 318-0476
        </li>
        <li class="contact__item">
          <svg class="contact__icon" viewBox="0 0 24 24" aria-hidden="true"><path fill="var(--orange)" d="M2 5h20v14H2z"/><path fill="none" stroke="var(--card-bottom)" stroke-width="1.8" d="M2.5 5.5 12 13l9.5-7.5"/></svg>
          info@falcridgehires.com
        </li>
        <li class="contact__item">
          <svg class="contact__icon" viewBox="0 0 24 24" aria-hidden="true"><circle cx="12" cy="12" r="10" fill="var(--orange)"/><path fill="none" stroke="var(--card-bottom)" stroke-width="1.5" d="M2 12h20M12 2c3 3 3 17 0 20M12 2c-3 3-3 17 0 20"/></svg>
          www.falcridgehires.com
        </li>
      </ul>
    </div>
  </section>

</body>
</html>
```